Product Label Design

Need a product design for our Epsom salt product, needs to have a luxurious simple feel to it. The picture attached is our brand and wordage on it, the bag we think should be a stand up bag that should be offwhite/creme color. The other picture are products that we like. We updated the packaging to be a Kraft tube box, please see the attached photo for dimensions.

```html
<!DOCTYPE html>
<html lang="en">
<head>
<meta charset="utf-8">
<title>ORVELLA Revive – Label Options</title>
<link rel="stylesheet" href="https://fonts.googleapis.com/css2?family=Hanken+Grotesk:wght@400;500;600&display=swap">
<style>
  :root {
    --page-bg: #fdfdfd;
    --label-bg: #f9f8f5;
    --ink: #6a6b6e;
    --ink-soft: #78797c;
    --brand-ink: #5f6064;
    --caption: #9a9a9c;
    --accent: #9dc1c6;
    --rule: #a9aaad;
  }
  * { margin: 0; padding: 0; box-sizing: border-box; }
  html, body {
    width: 1200px;
    height: 808px;
    overflow: hidden;
    background: var(--page-bg);
    font-family: "Hanken Grotesk", Arial, sans-serif;
  }
  .board { position: relative; width: 1200px; height: 808px; }

  .option-title {
    position: absolute;
    top: 59px;
    transform: translate(-50%, -50%);
    font-size: 27px;
    font-weight: 500;
    letter-spacing: 0.08em;
    color: var(--caption);
    white-space: nowrap;
  }
  .option-title--a { left: 273px; }
  .option-title--b { left: 875px; }

  .label {
    position: absolute;
    top: 104px;
    width: 453px;
    height: 651px;
    border-radius: 18px;
    background: var(--label-bg);
    box-shadow: 0 0 10px rgba(0, 0, 0, 0.02);
  }
  .label--a { left: 49px; }
  .label--b { left: 649px; }

  .label__line {
    position: absolute;
    left: 0;
    width: 100%;
    text-align: center;
    transform: translateY(-50%);
    line-height: 1;
    color: var(--ink);
    white-space: nowrap;
  }

  .brand { color: var(--brand-ink); font-weight: 500; letter-spacing: 0.08em; }
  .label--a .brand { top: 71px; font-size: 28px; }
  .label--b .brand { top: 113px; font-size: 58px; letter-spacing: 0.04em; }

  .rule {
    position: absolute;
    top: 193px;
    left: 47px;
    width: 360px;
    height: 1px;
    background: var(--rule);
  }

  .scent { color: var(--accent); font-weight: 600; letter-spacing: 0.14em; }
  .label--a .scent { top: 226px; font-size: 37px; }
  .label--b .scent { top: 249px; font-size: 28px; }

  .base { font-size: 21.5px; }
  .base-note { font-size: 17px; color: var(--ink-soft); }
  .label--b .base, .label--b .base-note { font-size: 21px; color: var(--ink); }

  .ingredient { font-size: 20px; }
  .label--b .ingredient { font-size: 20.5px; }

  .net-weight { top: 587px; font-size: 19.5px; color: var(--ink-soft); letter-spacing: 0.02em; }
</style>
</head>
<body>
<main class="board">
  <h2 class="option-title option-title--a">OPTION A</h2>
  <h2 class="option-title option-title--b">OPTION B</h2>

  <section class="label label--a">
    <p class="label__line brand">ORVELLA</p>
    <p class="label__line scent">REVIVE</p>
    <p class="label__line base" style="top:321px">Pure Epsom Salt</p>
    <p class="label__line base-note" style="top:349px">(Magnesium Sulfate)</p>
    <p class="label__line ingredient" style="top:409px">Infused with</p>
    <p class="label__line ingredient" style="top:446px">+ Abies sibirica</p>
    <p class="label__line ingredient" style="top:483px">+ Fir Balsam</p>
    <p class="label__line net-weight">NET WT. 3 LBS (1360 g)</p>
  </section>

  <section class="label label--b">
    <p class="label__line brand">ORVELLA</p>
    <div class="rule"></div>
    <p class="label__line scent">REVIVE</p>
    <p class="label__line base" style="top:324px">US Sourced Pure Epsom Salt</p>
    <p class="label__line base-note" style="top:357px">(Magnesium Sulfate)</p>
    <p class="label__line ingredient" style="top:415px">+ Abies sibirica</p>
    <p class="label__line ingredient" style="top:453px">+ Fir Balsam</p>
    <p class="label__line net-weight">NET WT. 3 LBS (1360 g)</p>
  </section>
</main>
</body>
</html>
```